New Business Card Design Project

Need a design that will create an impact / strong impression towards our clients for our business. We are in the lighting business and we do lighting retrofits for large commercial to industrial clientele.

Target Market(s)

Lighting Industry

Industry/Entity Type

Business

Font styles to use
Other font styles liked:
• we would like to use the font on our logo, not sure what it is though..

Requirements
Must have
• Our logo.
Nice to have
• We are open to suggestions that have to do with lighting.

```html
<!DOCTYPE html>
<html lang="en">
<head>
<meta charset="utf-8">
<title>Brightline Retrofit Co. — Business Card</title>
<link href="https://fonts.googleapis.com/css2?family=Roboto:wght@400;700&family=Roboto+Condensed:wght@700&display=swap" rel="stylesheet">
<style>
  :root {
    --backdrop: #574637;
    --card-white: #f2f2f2;
    --forest: #0e3a10;
    --leaf: #10862e;
    --body-grey: #4e4e4e;
    --divider: #b9b9b9;
    --on-dark: #ffffff;
  }
  * { margin: 0; padding: 0; box-sizing: border-box; }
  html, body { width: 1200px; height: 960px; overflow: hidden; }
  body {
    background: var(--backdrop);
    position: relative;
    font-family: "Roboto", Arial, sans-serif;
  }
  .card {
    position: absolute;
    width: 600px;
    height: 344px;
    box-shadow: 0 3px 5px rgba(0,0,0,0.45);
  }
  /* Front */
  .card-front { left: 314px; top: 113px; background: var(--card-white); }
  .front-brand {
    position: absolute; left: 58px; top: 140px;
    display: flex; align-items: center; gap: 10px;
  }
  .brand-mark { width: 18px; height: 18px; background: var(--leaf); }
  .brand-name {
    font-family: "Roboto", Arial, sans-serif;
    font-weight: 700; font-size: 23px; color: var(--forest);
    white-space: nowrap;
  }
  .divider {
    position: absolute; left: 318px; top: 72px;
    width: 1px; height: 186px; background: var(--divider);
  }
  .contact { position: absolute; left: 354px; top: 70px; }
  .person-name {
    font-family: "Roboto Condensed", Arial, sans-serif;
    font-weight: 700; font-size: 23px; color: var(--forest); line-height: 28px;
  }
  .person-title {
    font-family: "Roboto Condensed", Arial, sans-serif;
    font-weight: 700; font-size: 15px; color: var(--leaf); line-height: 20px;
  }
  .address {
    margin-top: 10px; font-size: 14px; line-height: 18px; color: var(--body-grey);
  }
  .contact-lines { margin-top: 10px; list-style: none; }
  .contact-lines li {
    display: flex; align-items: center; gap: 8px;
    font-size: 14px; line-height: 19px; color: var(--body-grey);
  }
  .contact-lines svg { width: 14px; height: 14px; fill: var(--forest); flex: none; }
  .front-rule {
    position: absolute; left: 0; right: 0; top: 311px; height: 2px; background: var(--leaf);
  }
  .front-band {
    position: absolute; left: 0; right: 0; bottom: 0; height: 29px;
    background: var(--forest); color: var(--on-dark);
    font-size: 14px; letter-spacing: 4.5px; text-align: center; line-height: 29px;
  }
  /* Back */
  .card-back { left: 311px; top: 472px; height: 343px; background: var(--forest); }
  .back-brand {
    position: absolute; left: 0; right: 0; top: 148px;
    display: flex; justify-content: center; align-items: center; gap: 14px;
  }
  .back-brand .brand-mark { width: 24px; height: 24px; background: #5bbd4f; }
  .back-brand .brand-name { font-size: 32px; color: var(--on-dark); }
  .back-web {
    position: absolute; left: 0; right: 0; top: 282px;
    text-align: center; color: var(--on-dark);
    font-size: 14px; letter-spacing: 2.2px;
  }
</style>
</head>
<body>
  <section class="card card-front">
    <div class="front-brand">
      <span class="brand-mark"></span>
      <span class="brand-name">Brightline Retrofit Co.</span>
    </div>
    <div class="divider"></div>
    <div class="contact">
      <p class="person-name">DANIEL REYES</p>
      <p class="person-title">CEO/FOUNDER</p>
      <p class="address">4120 Harbor View Road<br>Juneau, Alaska 99801</p>
      <ul class="contact-lines">
        <li><svg viewBox="0 0 24 24"><path d="M6.6 10.8a15 15 0 0 0 6.6 6.6l2.2-2.2c.3-.3.7-.4 1-.2 1.1.4 2.3.6 3.6.6.6 0 1 .4 1 1V20c0 .6-.4 1-1 1A17 17 0 0 1 3 4c0-.6.4-1 1-1h3.5c.6 0 1 .4 1 1 0 1.3.2 2.5.6 3.6.1.3 0 .7-.2 1z"/></svg>555 210 4471</li>
        <li><svg viewBox="0 0 24 24"><path d="M7 1h10a2 2 0 0 1 2 2v18a2 2 0 0 1-2 2H7a2 2 0 0 1-2-2V3a2 2 0 0 1 2-2zm0 3v14h10V4zm5 15.5a1 1 0 1 0 0 2 1 1 0 0 0 0-2z"/></svg>555 318 2096</li>
        <li><svg viewBox="0 0 24 24"><path d="M6 2h12v6H6zM3 9h18a2 2 0 0 1 2 2v7h-4v4H5v-4H1v-7a2 2 0 0 1 2-2zm4 6v5h10v-5z"/></svg>555 742 6150</li>
        <li><svg viewBox="0 0 24 24"><path d="M2 5h20v14H2zm2 2v.5l8 5 8-5V7l-8 5z"/></svg>daniel@brightlineco.com</li>
      </ul>
    </div>
    <div class="front-rule"></div>
    <div class="front-band">www.brightlineco.com</div>
  </section>

  <section class="card card-back">
    <div class="back-brand">
      <span class="brand-mark"></span>
      <span class="brand-name">Brightline Retrofit Co.</span>
    </div>
    <p class="back-web">www.brightlineretrofit.com</p>
  </section>
</body>
</html>
```